Small Business Broker Business Card Design

A business card design for a small business brokerage, which is a financial service, not unlike real estate brokerage, but for small businesses such as laundromats, pizza shops, restaurants, cleaners etc. The designs should all be simple, more conservative in nature, using the colors and font of the logo. Again, think real estate Brokerage as a business context
Contact Information for Business Card
Name: Glen R. Harlow. Title: Small Business Advisor. Email: g.harlow@bayfieldcapitalworks.example. Mobile: (555) 274-3918. Office: (555) 806-2147. www.bayfieldcapitalworks.example

```html
<!DOCTYPE html>
<html lang="en">
<head>
<meta charset="utf-8">
<title>Bayfield Capital Works – Business Card</title>
<link rel="stylesheet" href="https://fonts.googleapis.com/css2?family=Montserrat:wght@700&family=Roboto:wght@400;700&display=swap">
<style>
  :root{
    --navy:#1b3a6b;
    --green:#8cc63f;
    --ink:#1e1e1e;
    --paper:#ffffff;
    --backdrop:#232323;
  }
  *{box-sizing:border-box;margin:0;padding:0}
  html,body{width:1200px;height:780px;overflow:hidden;background:var(--backdrop)}
  .canvas{
    width:1200px;height:780px;
    display:flex;align-items:center;justify-content:center;gap:40px;
  }
  .card{
    position:relative;width:540px;height:309px;
    background:var(--paper);overflow:hidden;
  }
  .accent{position:absolute;width:12px;background:var(--green)}
  .accent--right{right:0;top:13%;height:34%}
  .accent--left{left:0;top:55%;height:38%}

  .brand{
    display:flex;align-items:center;gap:12px;
    font-family:"Montserrat",sans-serif;font-weight:700;
    color:var(--navy);text-transform:uppercase;letter-spacing:.04em;
  }
  .brand__mark{background:var(--green);flex:none}

  .card--front .brand{
    position:absolute;inset:0;justify-content:center;font-size:26px;
  }
  .card--front .brand__mark{width:22px;height:22px}

  .card--back .brand{
    position:absolute;left:34px;top:0;bottom:0;width:210px;font-size:15px;line-height:1.2;
  }
  .card--back .brand__mark{width:14px;height:14px}

  .divider{
    position:absolute;left:262px;top:70px;width:1px;height:170px;background:var(--ink);
  }
  .contact{
    position:absolute;left:286px;top:74px;
    font-family:"Roboto",sans-serif;color:var(--ink);
  }
  .contact__name{font-size:24px;font-weight:700;color:var(--green);line-height:1}
  .contact__title{font-size:12px;margin-top:4px}
  .contact__list{list-style:none;margin-top:20px}
  .contact__item{display:flex;align-items:center;gap:8px;font-size:11px;line-height:1;margin-bottom:7px}
  .contact__icon{width:12px;height:12px;flex:none}
</style>
</head>
<body>
<main class="canvas">

  <section class="card card--front" aria-label="Card front">
    <span class="accent accent--right"></span>
    <span class="accent accent--left"></span>
    <div class="brand">
      <span class="brand__mark"></span>
      <span class="brand__name">Bayfield Capital Works</span>
    </div>
  </section>

  <section class="card card--back" aria-label="Card back">
    <span class="accent accent--right"></span>
    <span class="accent accent--left"></span>
    <div class="brand">
      <span class="brand__mark"></span>
      <span class="brand__name">Bayfield Capital Works</span>
    </div>
    <span class="divider"></span>
    <div class="contact">
      <p class="contact__name">Glen R. Harlow</p>
      <p class="contact__title">Small Business Advisor</p>
      <ul class="contact__list">
        <li class="contact__item">
          <svg class="contact__icon" viewBox="0 0 12 12" aria-hidden="true"><rect x="3" y="0.5" width="6" height="11" rx="1.2" fill="none" stroke="var(--navy)" stroke-width="1.2"/><line x1="5" y1="9.6" x2="7" y2="9.6" stroke="var(--navy)"/></svg>
          (555) 274-3918
        </li>
        <li class="contact__item">
          <svg class="contact__icon" viewBox="0 0 12 12" aria-hidden="true"><path d="M2.5 1 L4.5 1 L5.3 3.6 L4 4.6 C4.7 6 6 7.3 7.4 8 L8.4 6.7 L11 7.5 L11 9.5 C11 10.3 10.3 11 9.5 11 C5 11 1 7 1 2.5 C1 1.7 1.7 1 2.5 1 Z" fill="var(--green)"/></svg>
          (555) 806-2147
        </li>
        <li class="contact__item">
          <svg class="contact__icon" viewBox="0 0 12 12" aria-hidden="true"><circle cx="6" cy="6" r="5.2" fill="none" stroke="var(--navy)" stroke-width="1.2"/><ellipse cx="6" cy="6" rx="2.2" ry="5.2" fill="none" stroke="var(--navy)"/><line x1="0.8" y1="6" x2="11.2" y2="6" stroke="var(--navy)"/></svg>
          www.bayfieldcapitalworks.example
        </li>
        <li class="contact__item">
          <svg class="contact__icon" viewBox="0 0 12 12" aria-hidden="true"><rect x="0.8" y="2.5" width="10.4" height="7.5" fill="none" stroke="var(--green)" stroke-width="1.2"/><polyline points="0.8,2.5 6,7 11.2,2.5" fill="none" stroke="var(--green)" stroke-width="1.2"/></svg>
          g.harlow@bayfieldcapitalworks.example
        </li>
      </ul>
    </div>
  </section>

</main>
</body>
</html>
```